KorvaNest - Home Income and Business Resources Platform

I am looking for a website template for a multi-purposed website. This website will feature:

1.) Website Directory with Ratings & comments on listings
2.) Company Blog
3.) Homepage with Content (see files for homepage mock)

I would like the Design to have a default width 1170px (wider then normal)

Of course I am looking for Pages for Listings to be designed.

Great looking BLOG Layout: http://journal.plimworks.example/html/blog.html

I would like 4 Versions of a Website Directory Listing "Box"
1.) Basic Listing Box
2.) Sponsored Listing Box
3.) Recommended Listing Box
4.) Stay Away From Listing Box

Information on the Listing Page (Like on a Category Page)
Site Name, Site URL, Website Image, # of Views, Rating and # of Comments

Information on the Listing Details Page:
Same as ABOVE + About website Description, Vornic Score, Category Information

Decent looking examples is here: https://samples.trevolin.example/directory/computers/ and http://www.zqrankhub.example/.

I will include some sketches and screenshots of things I like/looking for. As designers,you have creative freedom and are encouraged to show this. This is Phase one of this project and winning designer is guaranteed to have future work for this project.

Target Market(s)

Directory, business, websites

Industry/Entity Type

Business

Coding

Coded - Design and coding required

Number of Pages Required

5+ page

Font styles to use
Sans Serif

Colors

Designer to choose colors to be used in the design.

Requirements
Must have
• Professional yet clean look. The use of Icons & images
• Unique Look
Should not have
• Any exact copies of any examples I provided

```html
<!DOCTYPE html>
<html lang="en">
<head>
<meta charset="utf-8">
<title>KorvaNest – Home Income &amp; Business Resources</title>
<link href="https://fonts.googleapis.com/css2?family=Montserrat:wght@500;600;700&family=Open+Sans:wght@400;600&display=swap" rel="stylesheet">
<style>
:root{
  --accent:#f08a24;
  --navy:#2b3650;
  --navy-deep:#1d2436;
  --ink:#3a3a3a;
  --body:#666;
  --link-blue:#1a73c4;
  --blue:#1376c4;
  --red:#d04444;
  --green:#4a9d1a;
  --white:#fff;
  --rule:#e3e3e3;
  --footer:#151515;
}
*{box-sizing:border-box;margin:0;padding:0}
html,body{width:1200px;height:951px;overflow:hidden}
body{position:relative;font-family:"Open Sans",sans-serif;color:var(--white);background:var(--navy-deep)}
.backdrop{position:absolute;inset:0;background:linear-gradient(180deg,#34405c 0%,#2d3650 35%,#3a3a44 70%,#3b2e25 88%,#222 100%)}
.top-bar{position:absolute;top:0;left:0;width:1200px;height:3px;background:var(--accent)}
.site-header{position:absolute;top:3px;left:0;width:1200px;height:89px;border-bottom:1px solid rgba(255,255,255,.25)}
.brand{position:absolute;left:97px;top:28px;font-family:"Montserrat",sans-serif;font-weight:700;font-size:22px;letter-spacing:.2px}
.main-nav span{position:absolute;top:34px;font-family:"Montserrat",sans-serif;font-weight:600;font-size:14px;white-space:nowrap}
.search-icon{position:absolute;left:987px;top:37px}
.login{position:absolute;left:1021px;top:24px;width:80px;height:35px;border:1px solid rgba(255,255,255,.6);display:flex;align-items:center;justify-content:center;gap:6px;color:var(--accent);font-family:"Montserrat",sans-serif;font-weight:600;font-size:14px}
.about{position:absolute;left:99px;top:166px;width:758px;height:265px;background:#fff;border:3px solid #fff;overflow:hidden}
.about-photo{position:absolute;left:0;top:0;width:100%;height:100%;background:linear-gradient(90deg,#b9a999 0%,#d8ccc2 28%,#f4f3f1 48%,#f7f7f7 100%)}
.about-text h1{position:absolute;left:326px;top:24px;font-family:"Montserrat",sans-serif;font-weight:600;font-size:21px;color:var(--ink);white-space:nowrap}
.about-text h2{position:absolute;left:326px;top:61px;font-family:"Open Sans",sans-serif;font-weight:600;font-size:15.3px;color:var(--link-blue);white-space:nowrap}
.about-text p{position:absolute;left:326px;top:98px;width:402px;font-size:12px;line-height:22.3px;color:var(--body)}
.btn-outline{position:absolute;left:326px;top:201px;height:31px;padding:0 11px;line-height:29px;border:1px solid #aaa;color:var(--accent);font-family:"Montserrat",sans-serif;font-weight:700;font-size:11.5px}
.cards{position:absolute;left:99px;top:458px;display:flex;gap:22px}
.card{position:relative;width:238px;height:348px;border:3px solid;border-bottom:0;overflow:hidden}
.card.blue{background:var(--blue);border-color:var(--blue)}
.card.red{background:var(--red);border-color:var(--red)}
.card.green{background:var(--green);border-color:var(--green)}
.card-photo{height:136px}
.blue .card-photo{background:linear-gradient(135deg,#e9e6e8,#cfc7c6 60%,#9d8f88)}
.red .card-photo{background:linear-gradient(135deg,#c29a6e,#e9d9bd 55%,#6b5c4d)}
.green .card-photo{background:linear-gradient(135deg,#7fa0c8,#2f5387 55%,#c7d6ea)}
.card-head{position:absolute;left:14px;right:22px;top:148px;height:59px;display:flex;align-items:center;gap:9px;border-bottom:1px solid rgba(255,255,255,.55);padding-bottom:6px;font-family:"Montserrat",sans-serif;font-weight:600;font-size:13.5px;line-height:17px;text-transform:uppercase;white-space:nowrap}
.card p{position:absolute;left:14px;width:214px;top:222px;font-size:12.2px;line-height:21.5px;letter-spacing:-.1px}
.card .more{position:absolute;left:14px;top:317px;font-family:"Montserrat",sans-serif;font-weight:700;font-size:12px}
.sponsored{position:absolute;left:887px;top:166px;width:214px;height:389px;background:#fff}
.sponsored h3{height:50px;background:var(--accent);padding:13px 21px;font-family:"Montserrat",sans-serif;font-weight:600;font-size:20px}
.sponsor-list{list-style:none;margin:0 13px}
.sponsor-list li{display:flex;align-items:center;justify-content:space-between;height:81px;border-bottom:1px solid var(--rule);color:#333;font-size:13.5px;white-space:nowrap}
.sponsor-list li:nth-child(2){height:95px}
.sponsor-list li:nth-child(3){height:84px}
.sponsor-list li:last-child{height:79px;border-bottom:0}
.sponsor-name{display:flex;align-items:center;gap:6px;font-family:"Montserrat",sans-serif;font-weight:700;font-size:16px;color:#1f4fa0}
.sponsor-name i{width:9px;height:9px;background:#1f4fa0;display:block}
.promo{position:absolute;left:887px;top:591px;width:214px;height:215px;border:3px solid #fff;background:linear-gradient(180deg,#f4ecd9,#e9dfc8 80%,#b9651f 86%,#9a4e14)}
.site-footer{position:absolute;left:0;top:883px;width:1200px;height:68px;background:var(--footer);text-align:center;padding-top:25px;font-size:12.5px}
</style>
</head>
<body>
<div class="backdrop" role="img" aria-label="Evening photo of a suburban house with a lit porch and front lawn"></div>
<div class="top-bar"></div>
<header class="site-header">
  <div class="brand">KORVANEST</div>
  <nav class="main-nav">
    <span style="left:330px">HOME</span>
    <span style="left:406px">ABOUT US</span>
    <span style="left:511px">RESOURCES</span>
    <span style="left:626px">BUSINESS DIRECTORY</span>
    <span style="left:812px">NEWS</span>
    <span style="left:886px">CONTACT</span>
  </nav>
  <svg class="search-icon" width="15" height="15" viewBox="0 0 15 15"><circle cx="6" cy="6" r="4.5" fill="none" stroke="#fff" stroke-width="2"/><line x1="9.5" y1="9.5" x2="13.5" y2="13.5" stroke="#fff" stroke-width="2.4" stroke-linecap="round"/></svg>
  <div class="login"><svg width="10" height="13" viewBox="0 0 10 13"><path d="M2.5 6V4a2.5 2.5 0 0 1 5 0v2" fill="none" stroke="#f08a24" stroke-width="1.6"/><rect x="0.5" y="6" width="9" height="7" rx="1" fill="#f08a24"/></svg>LOGIN</div>
</header>

<section class="about">
  <div class="about-photo" role="img" aria-label="Smiling couple sitting together looking at a laptop"></div>
  <div class="about-text">
    <h1>ABOUT KORVANEST</h1>
    <h2>We are Home Income &amp; Business resources directory.</h2>
    <p>At vero eos et accusamus et iusto odio dignissimos ducimus qui bland itiis praesentium voluptatum deleniti atque corrupti quos dolores etqu as molestias excepturi sint occaecati cupiditate non provident, simique sunt in culpa qui officia deserunt moll.</p>
    <span class="btn-outline">READ MORE</span>
  </div>
</section>

<div class="cards">
  <article class="card blue">
    <div class="card-photo" role="img" aria-label="Small model house with keys and a fountain pen on paperwork"></div>
    <div class="card-head">
      <svg width="28" height="36" viewBox="0 0 28 36"><path d="M0 0h19l9 9v27H0z" fill="#fff"/><path d="M19 0v9h9" fill="#cfe3f5"/><g stroke="#1376c4" stroke-width="2.2"><line x1="7" y1="18" x2="21" y2="18"/><line x1="7" y1="23" x2="21" y2="23"/><line x1="7" y1="28" x2="21" y2="28"/></g></svg>
      <span>Home Income<br>Resource Directory</span>
    </div>
    <p>Find what you need, when you need it.The KorvaNest website directory is your one-stop pit for anything involved in making money</p>
    <span class="more">LEARN MORE</span>
  </article>
  <article class="card red">
    <div class="card-photo" role="img" aria-label="Two people reviewing documents on a sunlit desk"></div>
    <div class="card-head">
      <svg width="46" height="32" viewBox="0 0 46 32"><rect x="6" y="2" width="34" height="23" rx="2" fill="none" stroke="#fff" stroke-width="2.6"/><path d="M0 28h46v2a2 2 0 0 1-2 2H2a2 2 0 0 1-2-2z" fill="#fff"/></svg>
      <span>Advertising<br>Benefits</span>
    </div>
    <p>Everyone needs to advertise and we know just how to get your offer out to the right people. We have many methods including</p>
    <span class="more">LEARN MORE</span>
  </article>
  <article class="card green">
    <div class="card-photo" role="img" aria-label="Hand touching a rising bar chart on a blue screen"></div>
    <div class="card-head">
      <svg width="28" height="44" viewBox="0 0 28 44"><line x1="14" y1="1" x2="14" y2="43" stroke="#fff" stroke-width="3"/><path d="M24 12c-2-4-6-5-10-5-5 0-9 3-9 7 0 9 19 5 19 14 0 4-4 7-10 7-4 0-8-2-10-5" fill="none" stroke="#fff" stroke-width="4.5"/></svg>
      <span>Earning with<br>KorvaNest</span>
    </div>
    <p>Text: Join KorvaNest and start earning money. When you share KorvaNest and lock in an advertiser or premium listing, we reward you.</p>
    <span class="more">LEARN MORE</span>
  </article>
</div>

<aside class="sponsored">
  <h3>SPONSORED</h3>
  <ul class="sponsor-list">
    <li><span class="sponsor-name"><i></i>Ravlo</span><span>Lorem ipsum</span></li>
    <li><span class="sponsor-name"><i></i>Tessmark</span><span>Lorem ipsum</span></li>
    <li><span class="sponsor-name"><i></i>Kivo</span><span>Lorem ipsum</span></li>
    <li><span class="sponsor-name"><i></i>Brindle</span><span>Lorem ipsum</span></li>
  </ul>
</aside>

<div class="promo" role="img" aria-label="Advertisement: illustrated house frame with tools, promoting a home equity line of credit"></div>

<footer class="site-footer">Copyright © 2017. KorvaNest. All Rights Reserved.</footer>
</body>
</html>
```